Enlighted Feel-Good Wrapper Design for Cannabis Snack Bar: Vesko Bites.

We need a logo and wrapper for the first product in our line-up, Pip Crackle Maple! - Honey Salted Nuts and Dark Chocolate. Please highlight the name Maple Pip Crackle!, more than the name Vesko Bites or flavor of the bar. The package dimensions unfolded and unsealed are 6.5 inches x 5.25 inches. I have uploaded 3 photos of similar bar wrappers as an example of the wrapper type. The winning design will be awarded an extra amount for the Vesko Bites logo from Craft Hive.

It is a nut based snack bar similar to brands like Brisk, Stellar Munch, Orla, and Rover Bars. The difference is that this bar will contain THC and/or CBD oils. It is designed for the Medical Marijuana market in California. I would like the bar to be more upscale in design as we are going after a demographic with a higher disposable income and will be in their 30's-60's. We would like the brand to be appealing to both men and women. We would like the wrapper/logo to have an air of enlightenment to it. We want people to feel like they will be at peace when they eat this bar. Please do not make the design flashy, or decorated with marijuana leaves. We do not want something cheesy. We uploaded pictures of the bar so you can see what they look like. The packaging has to be OPAQUE.

Please include all the following. If you don't know specific values, weights or ingredients please fill the space with any text that can be substituted.

Label Regulatory Requirements:

(1) The identity of the product in a text size reasonably related to the most prominent printed matter on the panel;
(2) The words “cannabis-infused” immediately above the identity of the product in bold type and a text size larger than the text size used for the identity of the product;
(3) The cannabis product symbol uploaded in this post. The symbol shall be no smaller in size than half (.5) inch by half (.5) inch and shall be printed legibly and conspicuously;
(4) The net weight or volume of the contents of the package;

1.4 oz (40g)

(5) The THC content and CBD content for the package in its entirety, expressed in milligrams per package;

40mg

(6) The THC content and CBD content per serving, expressed in milligrams per serving;

10mg

(b) The primary panel text must be in type size no less than 6 point font and be in relation to the size of the primary panel and container.

40408. Informational Panel Labeling Requirements.
(a) The label for a medical cannabis product shall include an informational panel that includes the following:
(1) The licensed manufacturer and its contact number or website address;

Vesko Bites, San Diego, CA (555)302-7194, www.veskobites.example

(2) The date of manufacture;
(3) Each of the following statements:
(A) “SCHEDULE I CONTROLLED SUBSTANCE.”
(B) “KEEP OUT OF REACH OF CHILDREN AND ANIMALS” in bold print.
(C) “FOR MEDICAL USE ONLY.”
(D) “IF PREGNANT OR BREASTFEEDING, CONSULT A PHYSICIAN PRIOR TO USE.”
(E) “THE INTOXICATING EFFECTS OF THIS PRODUCT MAY BE DELAYED BY UP TO TWO HOURS.”
(F) “THIS PRODUCT MAY IMPAIR THE ABILITY TO DRIVE OR OPERATE MACHINERY, PLEASE USE EXTREME CAUTION.”
(4) A list of all product ingredients in descending order of predominance by weight or volume;

NUT MIXTURE:
almonds, peanuts, walnuts, puffed rice, flaxseed

SYRUP:
honey, brown rice syrup, sea salt, vanilla

CHOCOLATE DRIZZLE:
dark chocolate, coconut oil

(5) If an edible product that contains an ingredient, flavoring, coloring, or an incidental additive that bears or contains a major food allergen, the word “contains,” followed by a list of the applicable major food allergens;

Contains tree nuts.

(6) If an edible product, the names of any artificial food colorings contained in the product;
(7) If an edible product, the amount, in grams, of sodium, sugar, carbohydrates, and total fat per serving;

Dark Chocolate Sea Salt: 193 calories, 12.5g fat, 95mg sodium, 18.9g carbs, 2.1g fiber, 14g sugars, 5.2g protein

(8) The lot number;
(9) Instructions for use, such as the method of consumption or application, and any preparation necessary prior to use;
(10) The product expiration date, “use by” date, or “best by” date; and
(11) The unique identifier.
(b) The informational panel text shall be in a type size of no less than 6 point font and in relation to the size of the primary panel and container, unless there is insufficient area on the container available to print all the required information in a type size of no less than 6 point font. In such a case, the label shall include the warning statements required by paragraph (3) in a type size of no less than 6 point font, and the product shall be accompanied by a supplemental labeling that includes all of the information required by this section. The text of the supplemental labeling shall be no less than 8 point font.

The label shall not contain any of the following:

(a) Claims that the manufactured cannabis or cannabis product was grown in a California county when the cannabis was not grown there.
(b) The name of a California county unless the cannabis was grown there.
(c) Content that is or designed to be attractive to individuals under the age of 21, including but not limited to:
(1) Cartoons;
(2) Any likeness to images, characters, or phrases that are popularly used to advertise to children; or
(3) Any imitation of candy packaging or labeling.
(d) False labeling information. Labeling is false if it is false or misleading in any particular.
(e) Claims of health benefits or other physical benefits.
Updates

Industry/Entity Type

Retail

Logo Text

Vesko Bites

Colors

Designer to choose colors to be used in the design.

Requirements
Must have
• I would like to have a logo/icon of an cute owl or icon of a small tree branch with leaves and nut hanging off or anything else that you think would be a good logo incorporated with the company name "Vesko Bites." I uploaded a logo of an owl logo that I like. Feel free to adjust and create something creative, please do not copy it.
• The wrapper needs to reflect an upscale, natural, farm fresh, whole food product. We are trying to build a high end line of products that appeal to health conscious women and men ages 30 - 60 years old.
• Please include text from Allergen warning in one of the uploaded photos.
• Please add - "Gluten free" to the label, "Non GMO" or "GMO Free" and "No Soy" or "Soy Free", and "Dairy Free" as either writing or as an icon of some sort.
Nice to have
• Please see posted photos of some wrappers of food products that I like for ideas. Some color suggestions to incorporate: Red, Yellow, Green, Orange simply because these colors have been proven appealing to the eye for food labels. You may use one or a few of these and can balance them out with other colors. Please do not use traditional colors associated with cannabis such as dark brown or deep green. Subdued, natural looking versions of these may be okay if they are balanced out with other colors or the rest of the bar. I would also like the wrapper to have some graphics that can illustrate what the bar actually looks like so that people know whats inside!
• The final design should communicate:
• Freshness
• Organic
• Healthy
• Modern
Should not have
• I do not want this product to have graphics of typical cheesy cannabis/marijuana leaves or any other low class graphics related to the industry. Not graphics of marijuana flower, joints, smoke or leaves.

```html
<!DOCTYPE html>
<html lang="en">
<head>
<meta charset="utf-8">
<title>Vesko Bites – Maple Pip Crackle! wrapper</title>
<link rel="stylesheet" href="https://fonts.googleapis.com/css2?family=Kaushan+Script&family=Montserrat:wght@500&family=Oswald:wght@300;700&display=swap">
<style>
  :root {
    --bg-light: #f7f7f7;
    --bg-dark: #e6e6e6;
    --ink: #2b2b2b;
    --brand-grey: #3a3a3a;
    --orange: #f0a443;
    --orange-shade: #d9861f;
    --wrap-orange: #e4922b;
    --wrap-light: #f5b761;
    --wrap-dark: #c86f16;
    --white: #ffffff;
  }
  * { margin: 0; padding: 0; box-sizing: border-box; }
  html, body { width: 1200px; height: 784px; overflow: hidden; }
  body {
    position: relative;
    background: radial-gradient(ellipse at 50% 35%, var(--bg-light) 0%, var(--bg-dark) 100%);
  }

  .brand {
    position: absolute; left: 96px; top: 66px;
    display: flex; align-items: center; gap: 22px;
  }
  .brand-dot {
    width: 84px; height: 84px; border-radius: 50%;
    background: var(--brand-grey);
  }
  .brand-name {
    font-family: "Montserrat", sans-serif; font-weight: 500;
    font-size: 50px; line-height: 50px; color: var(--brand-grey);
    letter-spacing: -1px;
  }

  .headline {
    position: absolute; left: 440px; top: 46px;
    display: flex; align-items: baseline; white-space: nowrap;
  }
  .headline-script {
    font-family: "Kaushan Script", cursive; font-size: 74px;
    color: var(--ink); margin-right: 18px;
  }
  .headline-bold {
    font-family: "Oswald", sans-serif; font-weight: 700; font-size: 104px;
    color: var(--orange); text-transform: uppercase; line-height: 1;
    text-shadow: 4px 3px 0 var(--orange-shade);
  }

  .wrapper {
    position: absolute; left: 198px; top: 264px;
    width: 800px; height: 248px;
  }
  .wrapper-art { position: absolute; inset: 0; }

  .bar-photo {
    position: absolute; left: 40px; top: 82px; width: 268px; height: 132px;
    border-radius: 22px;
    background: linear-gradient(160deg, #e2c08a 0%, #c99a55 45%, #6b3f1d 100%);
    transform: rotate(8deg);
  }

  .wrap-brand {
    position: absolute; left: 254px; top: 26px;
    display: flex; align-items: center; gap: 6px;
  }
  .wrap-brand-dot { width: 26px; height: 26px; border-radius: 50%; background: var(--brand-grey); }
  .wrap-brand-name {
    font-family: "Montserrat", sans-serif; font-weight: 500;
    font-size: 15px; line-height: 15px; color: var(--brand-grey);
  }

  .wrap-title {
    position: absolute; left: 196px; top: 60px;
    display: flex; align-items: baseline; white-space: nowrap;
  }
  .wrap-title-script {
    font-family: "Kaushan Script", cursive; font-size: 38px;
    color: var(--ink); margin-right: 8px;
  }
  .wrap-title-bold {
    font-family: "Oswald", sans-serif; font-weight: 700; font-size: 54px;
    color: var(--orange); text-transform: uppercase; line-height: 1;
    text-shadow: 2px 2px 0 var(--orange-shade);
  }

  .flavor {
    position: absolute; left: 334px; top: 146px; width: 260px; height: 46px;
    border-radius: 24px; background: var(--wrap-orange);
    transform: rotate(-5deg);
    display: flex; align-items: center; justify-content: center;
    font-family: "Oswald", sans-serif; font-weight: 300; font-size: 15px;
    color: var(--white); text-transform: uppercase; white-space: nowrap;
  }
  .flavor-drop {
    position: absolute; left: 604px; top: 140px; width: 12px; height: 12px;
    border-radius: 50%; background: var(--wrap-orange);
  }
</style>
</head>
<body>
  <header class="brand">
    <span class="brand-dot"></span>
    <span class="brand-name">Vesko<br>Bites</span>
  </header>

  <h1 class="headline">
    <span class="headline-script">Maple Pip</span>
    <span class="headline-bold">Crackle!</span>
  </h1>

  <section class="wrapper">
    <svg class="wrapper-art" width="800" height="248" viewBox="0 0 800 248">
      <defs>
        <pattern id="teeth-left" width="10" height="10" patternUnits="userSpaceOnUse">
          <polygon points="0,0 10,5 0,10" fill="#000"/>
        </pattern>
        <pattern id="teeth-right" width="10" height="10" patternUnits="userSpaceOnUse" x="790">
          <polygon points="10,0 0,5 10,10" fill="#000"/>
        </pattern>
        <mask id="serrated-ends">
          <rect width="800" height="248" fill="#fff"/>
          <rect x="0" width="10" height="248" fill="url(#teeth-left)"/>
          <rect x="790" width="10" height="248" fill="url(#teeth-right)"/>
        </mask>
        <linearGradient id="end-left" x1="0" x2="1">
          <stop offset="0" stop-color="var(--wrap-dark)"/>
          <stop offset="1" stop-color="var(--wrap-orange)"/>
        </linearGradient>
      </defs>
      <g mask="url(#serrated-ends)">
        <rect width="800" height="248" fill="url(#end-left)"/>
        <path d="M0 60 Q70 20 160 0 L0 0 Z" fill="var(--wrap-light)" opacity="0.7"/>
        <path d="M0 248 L0 160 Q40 220 130 248 Z" fill="var(--wrap-light)" opacity="0.7"/>
        <path d="M700 0 L800 0 L800 248 L720 248 Q790 124 700 0 Z" fill="var(--wrap-light)"/>
        <path d="M120 16 L690 16 Q760 124 690 232 L120 232 Q40 124 120 16 Z" fill="var(--white)"/>
        <path d="M690 16 Q760 124 690 232 L706 232 Q776 124 706 16 Z" fill="var(--wrap-dark)" opacity="0.6"/>
      </g>
    </svg>

    <div class="bar-photo" role="img" aria-label="Photo of the nut bar drizzled with dark chocolate"></div>

    <div class="wrap-brand">
      <span class="wrap-brand-dot"></span>
      <span class="wrap-brand-name">Vesko<br>Bites</span>
    </div>

    <h2 class="wrap-title">
      <span class="wrap-title-script">Maple Pip</span>
      <span class="wrap-title-bold">Crackle!</span>
    </h2>

    <p class="flavor">Honey salted nuts and dark chocolate</p>
    <span class="flavor-drop"></span>
  </section>
</body>
</html>
```